Carpentry framing business card and logo design

We need a logo that works well with baseball caps, tee shirts and sweat shirts. We are a carpentry framing company specializing in apartment complexes and large residential communities. We work in what is known as the tri state area southeastern Pennsylvania , New Jersey and northern Delaware . We would like to see die signs using the old English letter M and royal blue colors. Also we stress OSHA compliance and safety.

Industry/Entity Type

Residential

Contact Information for Business Card

Valdrick Construction Co Inc
4870 Quillford Lane
Ambler PA 19087
Dale Valdrick
dale1valdrick@norvexmail.com
267-815-0926

```html
<!DOCTYPE html>
<html lang="en">
<head>
<meta charset="utf-8">
<title>Valdrick Construction Co Inc — Business Card</title>
<link rel="stylesheet" href="https://fonts.googleapis.com/css2?family=Roboto:wght@400;500&display=swap">
<style>
  :root {
    --stage: #e9e7e3;
    --card-white: #ffffff;
    --card-black: #0b0b0b;
    --ink: #2b2b2b;
    --ink-soft: #4a4a4a;
    --green: #7cc242;
  }
  * { box-sizing: border-box; margin: 0; padding: 0; }
  html, body { width: 1200px; height: 818px; overflow: hidden; }
  body {
    background: var(--stage);
    font-family: "Roboto", Arial, sans-serif;
    position: relative;
  }
  .card {
    position: absolute;
    top: 259px;
    width: 525px;
    height: 300px;
    overflow: hidden;
    box-shadow: 0 10px 28px rgba(0,0,0,.22);
  }
  .card--front { left: 50px; background: var(--card-white); }
  .card--back { left: 625px; background: var(--card-black); }
  .card__art { position: absolute; inset: 0; }

  .brand {
    position: absolute;
    left: 34px; top: 40px;
    display: flex; align-items: center; gap: 12px;
  }
  .brand__mark { width: 26px; height: 26px; background: var(--green); flex: none; }
  .brand__name {
    font-weight: 500; font-size: 19px; color: var(--green);
    letter-spacing: .3px; white-space: nowrap;
  }
  .brand__rule {
    position: absolute; left: 34px; top: 84px;
    width: 250px; height: 2px; background: var(--ink);
  }

  .holder {
    position: absolute; left: 34px; top: 116px;
    font-size: 24px; font-weight: 500; color: var(--ink);
  }
  .contacts {
    position: absolute; left: 34px; top: 160px;
    list-style: none;
  }
  .contacts li {
    display: flex; align-items: center; gap: 10px;
    font-size: 14px; color: var(--ink-soft);
    height: 24px; white-space: nowrap;
  }
  .contacts svg { width: 16px; height: 16px; flex: none; }
  .tagline {
    position: absolute; left: 34px; bottom: 30px;
    font-size: 16px; color: var(--green); white-space: nowrap;
  }
</style>
</head>
<body>

  <section class="card card--front" aria-label="Business card front">
    <svg class="card__art" viewBox="0 0 525 300" aria-hidden="true">
      <path d="M430 -10 C 560 40, 560 260, 450 320" fill="none" stroke="var(--green)" stroke-width="5"/>
    </svg>

    <div class="brand">
      <span class="brand__mark"></span>
      <span class="brand__name">Valdrick Construction Co Inc</span>
    </div>
    <div class="brand__rule"></div>

    <h1 class="holder">Dale Valdrick</h1>

    <ul class="contacts">
      <li>
        <svg viewBox="0 0 16 16" aria-hidden="true"><rect width="16" height="16" fill="var(--green)"/><path d="M4.5 3.5h2l1 2.5-1.2.8a6 6 0 0 0 2.9 2.9l.8-1.2 2.5 1v2a1 1 0 0 1-1 1A8.5 8.5 0 0 1 3.5 4.5a1 1 0 0 1 1-1z" fill="#fff"/></svg>
        267-815-0926
      </li>
      <li>
        <svg viewBox="0 0 16 16" aria-hidden="true"><rect width="16" height="16" fill="var(--green)"/><rect x="3" y="4.5" width="10" height="7" fill="none" stroke="#fff" stroke-width="1.2"/><path d="M3 4.5l5 4 5-4" fill="none" stroke="#fff" stroke-width="1.2"/></svg>
        dale1valdrick@norvexmail.com
      </li>
      <li>
        <svg viewBox="0 0 16 16" aria-hidden="true"><rect width="16" height="16" fill="var(--green)"/><path d="M8 2.8a3.6 3.6 0 0 0-3.6 3.6C4.4 9.2 8 13.2 8 13.2s3.6-4 3.6-6.8A3.6 3.6 0 0 0 8 2.8z" fill="#fff"/><circle cx="8" cy="6.4" r="1.3" fill="var(--green)"/></svg>
        4870 Quillford Lane Corlenne QV 19087
      </li>
    </ul>

    <p class="tagline">Jobsite safety always comes first</p>
  </section>

  <section class="card card--back" aria-label="Business card back">
    <svg class="card__art" viewBox="0 0 525 300" aria-hidden="true">
      <circle cx="330" cy="150" r="175" fill="var(--card-white)"/>
      <path d="M250 -20 C 400 10, 450 200, 330 330" fill="none" stroke="var(--green)" stroke-width="6"/>
    </svg>
  </section>

</body>
</html>
```